Stonebrace Business Card Design

The Stonebrace Co is an aggregate (crushing) equipment dealer serving Western Canadian provinces. Stonebrace is a distributor of aggregate equipment for different manufacturers.

We are looking to change and update the existing business card which has been used since the existence of the company. A copy of existing card has been attached for reference. The Stonebrace Co logo we want to remain the same and we want the green color to remain the same.

We are wanting something new with a different look. A refreshing card to show a new modern and updated look. No longer wanting to have the manufacturers on the back of the card but something more like our logo on the back of the card with a statement like "Crushing Solutions"

ideas could be:
- card can be different colors on front and back
- front or reverse of the card could possibly be the green color with the logo in black

Target Market(s)

Owners of Aggregate/Crushing companies

Contact Information for Business Card

see above

Requirements
Must have
• - logo to remain same along with same font within logo
• - green color to remain same
Nice to have
• as noted above under project description
Should not have

```html
<!DOCTYPE html>
<html lang="en">
<head>
<meta charset="utf-8">
<title>The Stonebrace Co. — Business Card</title>
<link rel="stylesheet" href="https://fonts.googleapis.com/css2?family=Arimo:wght@400;700&display=swap">
<style>
  :root {
    --olive: #878c0b;
    --ink: #231f20;
    --paper: #ffffff;
    --paper-grey: #ececec;
    --backdrop: #dcdad8;
    --text-light: #e6e6e6;
    --text-dark: #1d1d1b;
  }
  * { box-sizing: border-box; margin: 0; padding: 0; }
  html, body {
    width: 1200px; height: 900px; overflow: hidden;
    background: var(--backdrop);
    font-family: "Arimo", Arial, sans-serif;
  }
  .canvas { position: relative; width: 1200px; height: 900px; }

  .card { position: absolute; box-shadow: 0 6px 18px rgba(0,0,0,0.18); overflow: hidden; }

  /* Front */
  .card-front {
    left: 78px; top: 34px; width: 588px; height: 364px;
    background: var(--ink);
  }
  .card-front .side-band {
    position: absolute; left: 0; top: 0; width: 168px; height: 100%;
    background: var(--paper);
  }
  .card-front .contact {
    position: absolute; right: 38px; top: 58px;
    text-align: right; color: var(--text-light);
  }
  .contact .person-name {
    color: var(--olive); font-size: 21px; font-weight: 400;
    letter-spacing: 0.5px; margin-bottom: 56px;
  }
  .contact .lines { list-style: none; font-size: 16.5px; line-height: 21px; }
  .contact .lines li { display: flex; justify-content: flex-end; align-items: center; gap: 3px; }
  .contact .lines svg { width: 12px; height: 12px; fill: var(--olive); flex: none; }
  .contact .address { margin-top: 21px; font-size: 16.5px; line-height: 21px; font-style: normal; }

  /* Back */
  .card-back {
    left: 388px; top: 505px; width: 567px; height: 352px;
    background: var(--paper-grey);
  }
  .card-back .company {
    position: absolute; left: 0; right: 0; top: 196px;
    display: flex; justify-content: center; align-items: center; gap: 12px;
  }
  .company .dot { width: 18px; height: 18px; border-radius: 50%; background: var(--olive); }
  .company .company-name {
    font-size: 22px; font-weight: 700; color: var(--text-dark); letter-spacing: 0.3px;
  }
  .card-back .tagline {
    position: absolute; left: 40px; right: 40px; top: 266px;
    display: flex; align-items: center; gap: 4px;
    font-size: 15px; font-weight: 700; color: #333; letter-spacing: 0.3px;
  }
  .tagline::before, .tagline::after {
    content: ""; flex: 1; height: 1px; background: var(--olive);
  }
</style>
</head>
<body>
<div class="canvas">

  <section class="card card-front">
    <div class="side-band"></div>
    <div class="contact">
      <h1 class="person-name">DEREK HALVORSEN</h1>
      <ul class="lines">
        <li>780.555.0148(Direct)<svg viewBox="0 0 12 12"><path d="M1 4c0-2 2-3 5-3s5 1 5 3v1H8V4H4v1H1zM2 6h8l1 5H1z"/></svg></li>
        <li>780.555.0193<svg viewBox="0 0 12 12"><path d="M1 4c0-2 2-3 5-3s5 1 5 3v1H8V4H4v1H1zM2 6h8l1 5H1z"/></svg></li>
        <li>780.555.0126<svg viewBox="0 0 12 12"><path d="M3 0h6v12H3zM4 2v7h4V2z"/></svg></li>
        <li>derek@stonebr.com<svg viewBox="0 0 12 12"><path d="M0 2h12v8H0zM1 3l5 4 5-4z" fill-rule="evenodd"/></svg></li>
        <li>www.stonebrace.ca<svg viewBox="0 0 12 12"><circle cx="6" cy="6" r="5.5"/></svg></li>
      </ul>
      <address class="address">2218-48B Avenue<br>Leduc, Alberta T9E 1K7</address>
    </div>
  </section>

  <section class="card card-back">
    <div class="company">
      <span class="dot"></span>
      <span class="company-name">THE STONEBRACE CO.</span>
    </div>
    <p class="tagline">CRUSHING SOLUTIONS</p>
  </section>

</div>
</body>
</html>
```